Design a modern, classy & professional business card for an online real estate agency, specializing in medium-luxury properties in Thailand and later in Singapore and UK.

Possible design ideas so far: (not essential)

- curved corner(s) to the card, white on front & turquoise on back or visa versa.

- front of card - clear and simple, company name in metallic grey/monochrome, logo graphic & company name on front in spot UV or embossed/debossed effect.

- back of card - large, close-cropped, 'ghost' patterns of the C-shaped curves of logo, or company name repeated on back of card in spot UV.

Target Market(s)

- young to middle-aged professionals mainly (but ideally should design should suit all)

- UK, US,EU,AUS & ASIAN mainly (but ideally should design should suit all countries)

Industry/Entity Type

Real Estate

Requirements
Must have
• THEME:
- Luxurious & Modern
- Clean & striking
- Unique & creative

INFO:
- Logo & company name on front
- Contact details on back:

Tobias Hennlund
Managing Director

www.velmontestates.asia
www.velmontestates.co.uk

Tel: 083-274-6159
email: tobias@velmontestates.asia

(contact details can be displayed in any order as suites design.)

Nice to have
• - curved corner(s) to the card, white on front & turquoise on back or visa versa.

Should not have
• - No generic images of properties, palm trees/coconut trees etc.

- No other other bold colors, except for main turquoise, grey, metallic white & black theme.

- No obvious business card templates

```html
<!DOCTYPE html>
<html lang="en">
<head>
<meta charset="utf-8">
<title>Velmont Estates — Business Card</title>
<link rel="stylesheet" href="https://fonts.googleapis.com/css2?family=Cormorant+Garamond:wght@500&family=Montserrat:wght@400;500&display=swap">
<style>
  :root {
    --canvas: #ecebe8;
    --turquoise: #2cc5c1;
    --slate: #7b7c7e;
    --slate-light: #8a8b8d;
    --white: #ffffff;
    --ink-soft: rgba(255,255,255,0.88);
  }
  * { box-sizing: border-box; margin: 0; padding: 0; }
  html, body {
    width: 1075px; height: 1200px; overflow: hidden;
    background: var(--canvas);
  }
  .sheet {
    width: 1075px; height: 1200px;
    display: flex; flex-direction: column; align-items: center;
    padding-top: 52px; gap: 60px;
  }
  .card {
    position: relative;
    width: 900px; height: 514px;
    overflow: hidden;
    border-radius: 4px;
    box-shadow: 0 6px 18px rgba(0,0,0,0.18);
  }
  .card-shapes { position: absolute; inset: 0; }

  /* Front */
  .card--front { background: var(--turquoise); }
  .brand {
    position: absolute; left: 118px; top: 148px;
    display: flex; align-items: center; gap: 22px;
  }
  .brand-mark {
    width: 74px; height: 74px; background: var(--white);
  }
  .brand-name {
    font-family: "Cormorant Garamond", Georgia, serif;
    font-weight: 500; font-size: 58px; line-height: 1;
    color: var(--white); letter-spacing: 0.5px;
  }
  .holder {
    position: absolute; left: 218px; top: 262px;
    font-family: "Montserrat", Arial, sans-serif; color: var(--white);
  }
  .holder-name {
    font-size: 19px; font-weight: 500; letter-spacing: 2px; text-transform: uppercase;
  }
  .holder-role { font-size: 14px; margin-top: 6px; color: var(--ink-soft); }
  .contact {
    position: absolute; right: 58px; top: 70px;
    list-style: none;
    font-family: "Montserrat", Arial, sans-serif; font-size: 13px;
    color: var(--white); line-height: 1.95; text-align: right;
  }
  .contact li { display: flex; justify-content: flex-end; align-items: center; gap: 10px; }
  .contact svg { width: 12px; height: 12px; flex: none; }
  .contact .address { margin-bottom: 8px; }

  /* Back */
  .card--back { background: var(--slate); }
  .ghost-pattern {
    position: absolute; left: 0; top: 0; width: 640px; height: 100%;
    background: linear-gradient(135deg, var(--slate-light), var(--slate) 70%);
  }
  .back-brand {
    position: absolute; right: 64px; top: 50%; transform: translateY(-50%);
    font-family: "Cormorant Garamond", Georgia, serif;
    font-weight: 500; font-size: 56px; line-height: 1;
    color: var(--white);
  }
</style>
</head>
<body>
<main class="sheet">

  <section class="card card--front" aria-label="Card front">
    <svg class="card-shapes" viewBox="0 0 900 514" aria-hidden="true">
      <circle cx="0" cy="470" r="150" fill="none" stroke="#ffffff" stroke-width="46"/>
      <circle cx="470" cy="560" r="150" fill="none" stroke="#7b7c7e" stroke-width="50"/>
    </svg>

    <div class="brand">
      <span class="brand-mark"></span>
      <span class="brand-name">Velmont Estates</span>
    </div>

    <div class="holder">
      <p class="holder-name">Tobias Hennlund</p>
      <p class="holder-role">Managing Director</p>
    </div>

    <ul class="contact">
      <li class="address">Unit 4B, Fernhollow House<br>Marlow Lane, District 7
        <svg viewBox="0 0 12 12"><path d="M6 1a3.5 3.5 0 0 0-3.5 3.5C2.5 7.5 6 11 6 11s3.5-3.5 3.5-6.5A3.5 3.5 0 0 0 6 1z" fill="#fff"/></svg></li>
      <li>083-274-6159
        <svg viewBox="0 0 12 12"><path d="M3 1l2 2.5-1.2 1.2a7 7 0 0 0 3.5 3.5L8.5 7 11 9l-1.5 2A9 9 0 0 1 1 2.5z" fill="#fff"/></svg></li>
      <li>tobias@velmontestates.asia
        <svg viewBox="0 0 12 12"><rect x="1" y="2.5" width="10" height="7" fill="none" stroke="#fff"/><path d="M1 2.5l5 4 5-4" fill="none" stroke="#fff"/></svg></li>
      <li>www.velmontestates.asia
        <svg viewBox="0 0 12 12"><circle cx="6" cy="6" r="5" fill="none" stroke="#fff"/><path d="M1 6h10M6 1c2 2.5 2 7.5 0 10M6 1c-2 2.5-2 7.5 0 10" fill="none" stroke="#fff"/></svg></li>
      <li>www.velmontestates.co.uk
        <svg viewBox="0 0 12 12"><circle cx="6" cy="6" r="5" fill="none" stroke="#fff"/><path d="M1 6h10M6 1c2 2.5 2 7.5 0 10M6 1c-2 2.5-2 7.5 0 10" fill="none" stroke="#fff"/></svg></li>
    </ul>
  </section>

  <section class="card card--back" aria-label="Card back">
    <div class="ghost-pattern" role="img" aria-label="Faint repeated brand-symbol pattern in tone-on-tone grey"></div>
    <p class="back-brand">Velmont Estates</p>
  </section>

</main>
</body>
</html>
```